Dietary supplement, Clean and simple.

Hi,
I’d like to talk about the project,

About us:
We are a dietary supplement (Vitamins, Minerals, amino acids etc.) company.
The goal is to have about 25 products at the end of this year. However, for this goal to be achieved we need a good label design to make our products represent our company values.
I’ll be here every day supporting your questions, we are fully committed to making the highest/best quality/customer experience possible.

About the design and our values:
- Professional (We are in the industry of professionalism and expertise. I would love to show we are competent at this, Id. Like to have the labels looks like we have done our research.)
- Efficient (White spacing, good use of the space available.)
- Simple (Straight forward, in 5 seconds they have to know what the product they have is/how functions. We’re trying to simplify it for the consumer.
- No distractions (the only visually “distracting” factor can be the vector art.)

The guidelines:
The goal is to have a universal design, with one element that changes (Vector art). I’ll attach a file/multiple files I think can show some visuals on what I’m looking for, and what parts of the design I think are good/bad.

Label size: 69x155mm (Front is 77.5mm)

Design whatever you think fits our image. You’re the design expert, all I care about is that it fits our company standards/image.

Use this color/font.
Font: Sans Serif
Main company color is Mind green #237D62 (Use this color for something in the design.)

What I thought would be cool/might looks ugly, who knows:
1. The front of the label: Should have 1 vector art, preferably in the top right corner. (That looks good in multiple colors. The vector can have multiple areas to color, I would prefer 2 main colors in the vector art. The interchangeable colors are used for multiple kinds of products.)
2. Text/product information on the left. The text that will have to be displayed:
- Product name for instance “Magnesium + B6”
- Description for the product for instance “Magnesium with ginger taste”
- Company name or logo. (Add ® behind it. We are soon to be trademark registered.)
3. We need to show the "daily intake" amount on the front and also the amount in the complete bottle. For instance, “Daily intake 1 capsule, 60 capsules”.
• You don’t have to design the backside of the label. After I chose a design, I’d like to chat and give specific information on what areas need to be assigned where. (Too complex because of the law.)
Updates

Hi, Please make the deadline 31 days total. I want designers to have the time to design. And not be rushed to finish it.

I want to extend the deadline because i feel like a slightly more medical look would be interesting. Hope you can come up with something!!

Target Market(s)

Dietary supplement consumers

Industry/Entity Type

Dietary supplements

Font styles to use
Sans Serif

Colors

Designer to choose colors to be used in the design.

Requirements
Must have
• Trademark icon "®" has to be at the top right after the company logo(text of logo)/name.

```html
<!DOCTYPE html>
<html lang="en">
<head>
<meta charset="utf-8">
<title>Calm Crest Supplement Label Series</title>
<link href="https://fonts.googleapis.com/css2?family=Archivo:wght@800&family=Roboto+Condensed:wght@400;500;700&display=swap" rel="stylesheet">
<style>
  :root {
    --page: #efe9ee;
    --ink: #ffffff;
    --c-vitc-a: #a3ae6c; --c-vitc-b: #d6d14a;
    --c-gin-a: #f1b591;  --c-gin-b: #e8dcb4;
    --c-fish-a: #d8231b; --c-fish-b: #e2613f;
    --c-vita-a: #3b3030; --c-vita-b: #817d5f;
    --c-crea-a: #4a9a3c; --c-crea-b: #2b8a70;
    --c-multi-a: #e4520f; --c-multi-b: #f2ab1a;
    --c-d3-a: #f3c41a;   --c-d3-b: #c5d84c;
  }
  * { box-sizing: border-box; margin: 0; padding: 0; }
  html, body { width: 1200px; height: 1200px; overflow: hidden; }
  body {
    background: var(--page);
    font-family: "Roboto Condensed", Arial, sans-serif;
    color: var(--ink);
    position: relative;
  }
  .label-row {
    position: absolute;
    left: 0; width: 1200px;
    display: flex; justify-content: center; gap: 20px;
  }
  .label-row--top { top: 300px; }
  .label-row--bottom { top: 610px; }
  .label {
    position: relative;
    width: 270px; height: 280px;
    border-radius: 4px;
    overflow: hidden;
  }
  .label--vitc  { background: linear-gradient(160deg, var(--c-vitc-a), var(--c-vitc-b)); }
  .label--gin   { background: linear-gradient(160deg, var(--c-gin-a), var(--c-gin-b)); }
  .label--fish  { background: linear-gradient(160deg, var(--c-fish-a), var(--c-fish-b)); }
  .label--vita  { background: linear-gradient(160deg, var(--c-vita-a), var(--c-vita-b)); }
  .label--crea  { background: linear-gradient(160deg, var(--c-crea-a), var(--c-crea-b)); }
  .label--multi { background: linear-gradient(160deg, var(--c-multi-a), var(--c-multi-b)); }
  .label--d3    { background: linear-gradient(160deg, var(--c-d3-a), var(--c-d3-b)); }

  .brand {
    position: absolute; top: 52px; left: 0; width: 100%;
    text-align: center;
    font-weight: 700; font-size: 25px; letter-spacing: 0.5px;
    line-height: 1;
  }
  .brand sup { font-size: 10px; vertical-align: top; margin-left: 2px; }
  .brand-dot {
    display: block; width: 14px; height: 14px; border-radius: 50%;
    background: var(--ink); margin: 0 auto 8px;
  }
  .kind {
    position: absolute; left: 26px; top: 130px;
    font-size: 10.5px; line-height: 1.3; font-weight: 500;
  }
  .dose-dots {
    position: absolute; right: 40px; top: 131px;
    width: 30px;
  }
  .name {
    position: absolute; left: 26px; top: 162px;
    font-family: "Archivo", Arial, sans-serif;
    font-weight: 800; font-size: 24px; letter-spacing: -0.5px;
  }
  .benefit {
    position: absolute; left: 26px; top: 199px; width: 200px;
    font-size: 9.5px; line-height: 1.2; opacity: 0.95;
  }
  .count {
    position: absolute; left: 26px; top: 234px;
    font-size: 9.5px; font-weight: 500;
  }
  .per-day {
    position: absolute; right: 40px; top: 232px;
    display: flex; align-items: center; gap: 3px;
    font-size: 6px; line-height: 1; font-weight: 500;
  }
</style>
</head>
<body>
<svg width="0" height="0" style="position:absolute" aria-hidden="true">
  <defs>
    <g id="dots" fill="#fff">
      <circle cx="3" cy="3" r="2.6"/><circle cx="11" cy="3" r="2.6"/><circle cx="19" cy="3" r="2.6"/><circle cx="27" cy="3" r="2.6"/>
      <circle cx="3" cy="13" r="2.6"/><circle cx="11" cy="13" r="2.6"/><circle cx="19" cy="13" r="2.6"/><circle cx="27" cy="13" r="2.6"/>
    </g>
    <g id="caps" fill="#fff">
      <rect x="0" y="0" width="5" height="12" rx="2.5"/><rect x="6.5" y="0" width="5" height="12" rx="2.5"/>
    </g>
  </defs>
</svg>

<div class="label-row label-row--top">
  <section class="label label--vitc">
    <div class="brand"><span class="brand-dot"></span>CALM CREST<sup>®</sup></div>
    <p class="kind">Dietry Supplement<br>Vitamin C + Vitamin D3</p>
    <svg class="dose-dots" viewBox="0 0 30 16"><use href="#dots"/></svg>
    <h2 class="name">VITAMIN C</h2>
    <p class="benefit">boosting antioxidant levels<br>lowering blood pressure, immunity</p>
    <p class="count">Contains 60 Capsules</p>
    <div class="per-day"><svg width="12" height="12" viewBox="0 0 12 12"><use href="#caps"/></svg><span>PER<br>DAY</span></div>
  </section>
  <section class="label label--gin">
    <div class="brand"><span class="brand-dot"></span>CALM CREST<sup>®</sup></div>
    <p class="kind">Dietry Supplement<br>Ginseng + Vitamin B2</p>
    <svg class="dose-dots" viewBox="0 0 30 16"><use href="#dots"/></svg>
    <h2 class="name">GINSENG</h2>
    <p class="benefit">reduces gas and improves digestion<br>relieve nausea, relieving pain</p>
    <p class="count">Contains 60 Capsules</p>
    <div class="per-day"><svg width="12" height="12" viewBox="0 0 12 12"><use href="#caps"/></svg><span>PER<br>DAY</span></div>
  </section>
  <section class="label label--fish">
    <div class="brand"><span class="brand-dot"></span>CALM CREST<sup>®</sup></div>
    <p class="kind">Dietry Supplement<br>Fish Oil + Vitamin B6</p>
    <svg class="dose-dots" viewBox="0 0 30 16"><use href="#dots"/></svg>
    <h2 class="name">FISH OIL</h2>
    <p class="benefit">lower blood pressure, reduce tryglycerides<br>slow the development of plaque in arteries</p>
    <p class="count">Contains 60 Capsules</p>
    <div class="per-day"><svg width="12" height="12" viewBox="0 0 12 12"><use href="#caps"/></svg><span>PER<br>DAY</span></div>
  </section>
</div>

<div class="label-row label-row--bottom">
  <section class="label label--vita">
    <div class="brand"><span class="brand-dot"></span>CALM CREST<sup>®</sup></div>
    <p class="kind">Dietry Supplement<br>Vitamin A + Calcium</p>
    <svg class="dose-dots" viewBox="0 0 30 16"><use href="#dots"/></svg>
    <h2 class="name">VITAMIN A</h2>
    <p class="benefit">improve vision, strengthen immune<br>maintain healthy skin, heart and lungs</p>
    <p class="count">Contains 60 Capsules</p>
    <div class="per-day"><svg width="12" height="12" viewBox="0 0 12 12"><use href="#caps"/></svg><span>PER<br>DAY</span></div>
  </section>
  <section class="label label--crea">
    <div class="brand"><span class="brand-dot"></span>CALM CREST<sup>®</sup></div>
    <p class="kind">Dietry Supplement</p>
    <svg class="dose-dots" viewBox="0 0 30 16"><use href="#dots"/></svg>
    <h2 class="name">CREATINE</h2>
    <p class="benefit">improve athletic performance<br>increase muscle mass</p>
    <p class="count">Contains 60 Capsules</p>
    <div class="per-day"><svg width="12" height="12" viewBox="0 0 12 12"><use href="#caps"/></svg><span>PER<br>DAY</span></div>
  </section>
  <section class="label label--multi">
    <div class="brand"><span class="brand-dot"></span>CALM CREST<sup>®</sup></div>
    <p class="kind">Dietry Supplement<br>Multivitamin + B3</p>
    <svg class="dose-dots" viewBox="0 0 30 16"><use href="#dots"/></svg>
    <h2 class="name">MULTIVITAMIN</h2>
    <p class="benefit">reduces stress, improved short term memory<br>maintain muscle strength</p>
    <p class="count">Contains 60 Capsules</p>
    <div class="per-day"><svg width="12" height="12" viewBox="0 0 12 12"><use href="#caps"/></svg><span>PER<br>DAY</span></div>
  </section>
  <section class="label label--d3">
    <div class="brand"><span class="brand-dot"></span>CALM CREST<sup>®</sup></div>
    <p class="kind">Dietry Supplement<br>Vitamin D3 + Calcium</p>
    <svg class="dose-dots" viewBox="0 0 30 16"><use href="#dots"/></svg>
    <h2 class="name">VITAMIN D3</h2>
    <p class="benefit">strengthen bones, mood boost<br>and brain function improve</p>
    <p class="count">Contains 60 Capsules</p>
    <div class="per-day"><svg width="12" height="12" viewBox="0 0 12 12"><use href="#caps"/></svg><span>PER<br>DAY</span></div>
  </section>
</div>
</body>
</html>
```